Label design for an exciting new Vodka brand

We need a label design for a dynamic new Vodka brand called 'Pale lantern drift Vodka'. It is a crisp and versatile liquid with a clean and smooth finish. It should appeal to 21-39 year olds, with a slight female skew. Colours, fonts and styles should be modern and relatively neutral - take inspiration from the brand pictures attached.

Target Market(s)

21-39 year olds, both male and female, but with a slight female skew

```html
<!DOCTYPE html>
<html lang="en">
<head>
<meta charset="UTF-8">
<title>Pale lantern drift Vodka — Label</title>
<link href="https://fonts.googleapis.com/css2?family=Great+Vibes&family=Montserrat:wght@600;700&family=Barlow+Condensed:wght@300;400&display=swap" rel="stylesheet">
<style>
  :root {
    --page: #f4f4f4;
    --sand: #d9c0a6;
    --sand-light: #e8d6c4;
    --sand-deep: #c9ab8d;
    --paper: #ffffff;
    --ink: #2a2a2a;
    --ink-soft: #555555;
    --tan-text: #d3b99c;
    --foil-light: #f2f2f2;
    --foil-mid: #bdbdbd;
    --foil-dark: #6f6f6f;
  }
  * { margin: 0; padding: 0; box-sizing: border-box; }
  html, body { width: 1200px; height: 1200px; overflow: hidden; }
  body {
    background: var(--page);
    display: flex;
    align-items: center;
    justify-content: center;
  }
  .label {
    width: 716px;
    height: 1100px;
    display: flex;
    flex-direction: column;
    box-shadow: 0 6px 24px rgba(0,0,0,0.08);
  }
  .label-top {
    position: relative;
    height: 798px;
    background: linear-gradient(100deg, var(--sand-light) 0%, var(--sand-deep) 45%, var(--sand-light) 100%);
  }
  .brand-mark {
    position: absolute;
    top: 170px;
    right: 70px;
    width: 330px;
    text-align: center;
    font-family: "Montserrat", sans-serif;
    font-weight: 600;
    font-size: 26px;
    letter-spacing: 0.12em;
    color: rgba(255,255,255,0.35);
  }
  .brand-script {
    position: absolute;
    left: 60px;
    top: 450px;
    font-family: "Great Vibes", cursive;
    font-size: 104px;
    line-height: 1;
    color: var(--paper);
  }
  .brand-title {
    position: absolute;
    left: 56px;
    right: 56px;
    top: 565px;
    font-family: "Montserrat", sans-serif;
    font-weight: 700;
    font-size: 178px;
    line-height: 1;
    letter-spacing: -0.01em;
    text-align: center;
    background: linear-gradient(90deg, var(--foil-light) 0%, var(--foil-mid) 25%, var(--foil-dark) 55%, var(--foil-mid) 80%, var(--foil-light) 100%);
    -webkit-background-clip: text;
    background-clip: text;
    color: transparent;
  }
  .label-bottom {
    flex: 1;
    background: var(--paper);
    display: flex;
    flex-direction: column;
    align-items: center;
    padding-top: 50px;
  }
  .product-type {
    font-family: "Montserrat", sans-serif;
    font-weight: 700;
    font-size: 70px;
    letter-spacing: 0.12em;
    line-height: 1;
    color: var(--ink);
  }
  .tagline {
    margin-top: 14px;
    font-family: "Barlow Condensed", sans-serif;
    font-weight: 400;
    font-size: 27px;
    letter-spacing: 0.1em;
    color: var(--tan-text);
  }
  .spec-rule {
    margin-top: 34px;
    width: 628px;
    height: 1px;
    background: var(--ink-soft);
  }
  .spec-row {
    display: flex;
    align-items: center;
    margin-top: 8px;
    font-family: "Barlow Condensed", sans-serif;
    font-weight: 300;
    font-size: 25px;
    color: var(--ink-soft);
  }
  .spec-item { padding: 0 18px; }
  .spec-divider { width: 1px; height: 46px; background: var(--ink-soft); }
  .spec-batch { word-spacing: 0.3em; }
</style>
</head>
<body>
  <main class="label">
    <section class="label-top">
      <div class="brand-mark">PALE LANTERN DRIFT</div>
      <div class="brand-script">Pale lantern</div>
      <h1 class="brand-title">DRIFT</h1>
    </section>
    <section class="label-bottom">
      <h2 class="product-type">VODKA</h2>
      <p class="tagline">CLEAN AND SMOOTH FINISH</p>
      <div class="spec-rule"></div>
      <div class="spec-row">
        <span class="spec-item">NET.WT.750 ML</span>
        <span class="spec-divider"></span>
        <span class="spec-item spec-batch">SMALL BATCH &nbsp;HAND CRAFTED</span>
        <span class="spec-divider"></span>
        <span class="spec-item">40% ALC/VOL</span>
      </div>
    </section>
  </main>
</body>
</html>
```